Vitamin B12 Liquid Drops Label

hi, i need a label designed for my vitamin b12 drops that i am going to be selling on shopzello. the label needs to quickly capture the attention of a buyer as he or she is scrolling through the thumbnail search results on shopzello.com my brand is called nralo. i already have an example brand logo i will be using, however, i need help designing the rest of the label. attached are some examples of labels i like for other supplements.some of these examples are pink. i do not want pink. please go for a blue/green color scheme. THE DESIGN MUST BE BOLD

Target Market(s)

adults ages 30 - 64

Font styles to use
Sans Serif

Colors
0455a3
cedeed
3176b5
85acd3
cfdeed
9bcb3b
abd037
cadf82
00a990

Requirements
Must have
• - bold design
• - somewhat gender-neutral color scheme because this will be used equally by men and women
• - B12 MUST be very prominent and visible on the label
Should not have
• - it should not be "crunchy" looking

```html
<!DOCTYPE html>
<html lang="en">
<head>
<meta charset="utf-8">
<title>Vitamin B12 Methylcobamalin – Nralo</title>
<link rel="stylesheet" href="https://fonts.googleapis.com/css2?family=Roboto+Condensed:wght@400;700&display=swap">
<style>
  :root {
    --page-bg: #cedeed;
    --label-green: #9bcb3b;
    --label-blue: #0455a3;
    --title-blue: #0455a3;
    --accent-green: #cadf82;
  }
  html, body {
    margin: 0;
    padding: 0;
    width: 1200px;
    height: 800px;
    overflow: hidden;
    background: var(--page-bg);
  }
  .canvas {
    position: relative;
    width: 1200px;
    height: 800px;
  }
  .label-face {
    position: absolute;
    left: 428px;
    top: 40px;
    width: 344px;
    height: 720px;
  }
  .label-face text {
    font-family: "Roboto Condensed", "Arial Narrow", sans-serif;
  }
  .product-title {
    fill: var(--title-blue);
    font-weight: 700;
    font-size: 72px;
  }
  .ingredient-name {
    fill: var(--accent-green);
    font-weight: 700;
    font-size: 23px;
    letter-spacing: 4px;
  }
  .brand-name {
    fill: var(--accent-green);
    font-weight: 700;
    font-size: 60px;
  }
</style>
</head>
<body>
  <main class="canvas">
    <svg class="label-face" viewBox="0 0 340 710" xmlns="http://www.w3.org/2000/svg" role="group" aria-label="Vitamin B12 label front">
      <rect class="label-base" x="0" y="0" width="340" height="710" fill="var(--label-blue)"/>
      <polygon class="label-green-block" points="0,0 337,0 250,380 0,380" fill="var(--label-green)"/>
      <text class="product-title" x="16" y="354" textLength="212" lengthAdjust="spacingAndGlyphs">VITAMIN B12</text>
      <text class="ingredient-name" x="21" y="434" textLength="204" lengthAdjust="spacingAndGlyphs">METHYLCOBAMALIN</text>
      <text class="brand-name" x="186" y="660" textLength="134" lengthAdjust="spacingAndGlyphs">NRALO</text>
    </svg>
  </main>
</body>
</html>
```